Agriculture Business Card

I want to use my existing logo and use my tagline of "Don't Guess...Soil Test" on the card. Looking for a double sided card that will really get peoples attention.
Contact Info:
Marlow Field Crop Edge
Calvin Brusk
2917 K Lane
Larkin, NE 68593
402-555-0193
calvin.r.brusk@fieldmailbox.net

```html
<!DOCTYPE html>
<html lang="en">
<head>
<meta charset="utf-8">
<title>Marlow Field Crop Edge – Business Card</title>
<link rel="stylesheet" href="https://fonts.googleapis.com/css2?family=Arimo:wght@400&family=Fira+Sans+Condensed:wght@700&display=swap">
<style>
  :root {
    --backdrop: #1f1f1f;
    --card: #0c0c0c;
    --gold: #f6b21a;
    --brown: #8b5a41;
    --white: #f4f4f4;
    --rule: #5a5a5a;
  }
  * { box-sizing: border-box; margin: 0; padding: 0; }
  html, body { width: 1200px; height: 900px; overflow: hidden; }
  body {
    background: var(--backdrop);
    font-family: "Arimo", Arial, sans-serif;
    display: flex;
    flex-direction: column;
    align-items: center;
    justify-content: center;
    gap: 56px;
  }
  .card {
    width: 630px;
    height: 360px;
    background: var(--card);
    position: relative;
    display: flex;
    align-items: center;
  }
  .brand {
    display: flex;
    align-items: center;
    gap: 16px;
  }
  .brand-mark {
    width: 96px; height: 96px;
    border-radius: 50%;
    background: var(--gold);
    flex: none;
  }
  .brand-name {
    font-family: "Fira Sans Condensed", "Arial Narrow", sans-serif;
    font-weight: 700;
    color: var(--brown);
    font-size: 34px;
    line-height: 1.02;
  }
  .brand-name span { display: block; }

  /* front side */
  .card-front { padding: 0 0 0 36px; }
  .card-front .brand { width: 268px; }
  .divider {
    width: 1px; height: 190px;
    background: var(--rule);
    margin: 0 30px 0 12px;
  }
  .contact { display: flex; flex-direction: column; }
  .contact-name {
    font-family: "Fira Sans Condensed", "Arial Narrow", sans-serif;
    font-weight: 700;
    font-size: 32px;
    color: var(--brown);
    margin-bottom: 12px;
  }
  .contact-line {
    display: flex; align-items: center; gap: 8px;
    color: var(--white);
    font-size: 15px;
    line-height: 1.55;
  }
  .contact-line svg { width: 15px; height: 15px; flex: none; }
  .company { color: var(--brown); font-size: 16px; margin-top: 14px; line-height: 1.4; }
  .address { color: var(--white); font-size: 16px; line-height: 1.4; }

  /* back side */
  .card-back {
    flex-direction: column;
    justify-content: center;
    gap: 28px;
  }
  .card-back .brand-mark { width: 120px; height: 120px; }
  .card-back .brand-name { font-size: 44px; }
  .tagline {
    color: var(--gold);
    font-size: 20px;
    letter-spacing: 0.5px;
    text-transform: uppercase;
  }
</style>
</head>
<body>
  <section class="card card-front">
    <div class="brand">
      <span class="brand-mark"></span>
      <p class="brand-name"><span>Marlow Field</span><span>Crop Edge</span></p>
    </div>
    <div class="divider"></div>
    <div class="contact">
      <h1 class="contact-name">Calvin Brusk</h1>
      <p class="contact-line">
        <svg viewBox="0 0 24 24" aria-hidden="true"><path fill="#f6b21a" d="M6.6 10.8a15 15 0 0 0 6.6 6.6l2.2-2.2c.3-.3.7-.4 1-.2 1.1.4 2.3.6 3.6.6.6 0 1 .4 1 1V20c0 .6-.4 1-1 1A17 17 0 0 1 3 4c0-.6.4-1 1-1h3.5c.6 0 1 .4 1 1 0 1.3.2 2.5.6 3.6.1.3 0 .7-.2 1z"/></svg>
        402-555-0193
      </p>
      <p class="contact-line">
        <svg viewBox="0 0 24 24" aria-hidden="true"><path fill="#f6b21a" d="M2 5h20v14H2zm2 2v.4l8 5.2 8-5.2V7z"/></svg>
        calvin.r.brusk@fieldmailbox.net
      </p>
      <p class="company">Marlow Field Crop Edge</p>
      <p class="address">2917 K Lane, Larkin, NE 68593</p>
    </div>
  </section>

  <section class="card card-back">
    <div class="brand">
      <span class="brand-mark"></span>
      <p class="brand-name"><span>Marlow Field</span><span>Crop Edge</span></p>
    </div>
    <p class="tagline">Don't Guess...Soil Test</p>
  </section>
</body>
</html>
```